CalmPeak Nurses' Manifesto

Design a manifesto to inspire and motivate nurses to work at minimum standards of excellence in their nursing practice.

The manifesto will become a feature of our website, at conferences, workshops and retreats. It will also be featured on other marketing tools.

Primary Market:
Nurses and/or other healthcare professionals (specifically Doctors, Occupational Therapists, Psychologists and Social Workers).

However the manifesto is equally applicable to all nurses and healthcare professionals from new graduates to very experienced senior clinicians, administration officers,managers and healthcare executive personnel.

Mainly females and primarily 35 to 65 years old, which suggests people in this target age group have extensive experience, but have become jaded'.

The purpose of our business is to assist healthcare professionals, primarily nurses, to maintain their enthusiasm and excellence in service provision, for their benefit as well as the benefit of the clients.

I have attached:
File 1: Copy Samples and examples: which has the copy for the manifesto, examples that appeal to us and our 3 attempts.
File 2: Our colour Spec Sheet, HOWEVER the colours are not necessary limited to these colours. These colours are not in the logo that will be on the manifesto. The colours on the logo attached can/or also be used.
File 3: Prototype logo. The final logo will be available within 3 to 4 days.

Industry/Entity Type

Healthcare

Requirements
Must have
• Must use the copy as per the attached file.

It should be contemporary, eye catching and motivational.

Should not have
• MUST BE EASY TO READ. Each line MUST be clearly defined from each other.

```html
<!DOCTYPE html>
<html lang="en">
<head>
<meta charset="utf-8">
<title>CalmPeak Nurses' Manifesto</title>
<link rel="stylesheet" href="https://fonts.googleapis.com/css2?family=Bebas+Neue&family=Oswald:wght@600;700&display=swap">
<style>
  :root {
    --bg-deep: #2c4242;
    --bg-mid: #4a6664;
    --bg-light: #7d9996;
    --teal: #40d1c7;
    --orange: #f7943b;
    --green: #8cc83f;
    --white: #f3f3f1;
    --panel: #ffffff;
  }
  html, body {
    margin: 0;
    padding: 0;
    width: 810px;
    height: 1200px;
    overflow: hidden;
    background: var(--bg-deep);
  }
  .manifesto { display: block; width: 810px; height: 1200px; }
  .manifesto text {
    font-family: "Bebas Neue", "Oswald", sans-serif;
    text-transform: uppercase;
  }
  .manifesto .title {
    font-family: "Oswald", sans-serif;
    font-weight: 700;
    text-transform: none;
  }
  .teal { fill: var(--teal); }
  .orange { fill: var(--orange); }
  .green { fill: var(--green); }
  .white { fill: var(--white); }
  .brand-panel { fill: var(--panel); }
  .brand-dot { fill: var(--teal); }
  .manifesto .brand-name {
    font-family: "Oswald", sans-serif;
    font-weight: 600;
    text-transform: none;
    fill: var(--teal);
  }
</style>
</head>
<body>
<svg class="manifesto" viewBox="0 0 540 800" xmlns="http://www.w3.org/2000/svg" lengthAdjust="spacingAndGlyphs">
  <defs>
    <radialGradient id="backdrop" cx="62%" cy="38%" r="75%">
      <stop offset="0" stop-color="var(--bg-light)"/>
      <stop offset="0.45" stop-color="var(--bg-mid)"/>
      <stop offset="1" stop-color="var(--bg-deep)"/>
    </radialGradient>
  </defs>

  <rect class="backdrop" width="540" height="800" fill="url(#backdrop)" role="img" aria-label="Weathered dark teal textured backdrop"/>

  <!-- Heading -->
  <text class="title green" x="150" y="29" font-size="30" textLength="240" lengthAdjust="spacingAndGlyphs">Nurses' Manifesto</text>
  <text class="white" x="42" y="54" font-size="21" textLength="456" lengthAdjust="spacingAndGlyphs">Nurse with open hands, hearts and minds</text>
  <text class="teal" x="20" y="83" font-size="37" textLength="500" lengthAdjust="spacingAndGlyphs">Only follow exceptional leaders</text>

  <!-- Always lead -->
  <text class="orange" x="18" y="150" font-size="82" textLength="192" lengthAdjust="spacingAndGlyphs">Always</text>
  <text class="white" x="220" y="111" font-size="20" textLength="298" lengthAdjust="spacingAndGlyphs">Lead with purpose passion and commitment</text>
  <text class="orange" x="222" y="141" font-size="31" textLength="218" lengthAdjust="spacingAndGlyphs">Be solution focussed</text>

  <!-- Seek success column -->
  <text class="white" transform="translate(490 140) rotate(90)" font-size="50" textLength="540" lengthAdjust="spacingAndGlyphs">Seek success firstly from within</text>

  <!-- Unique -->
  <text class="teal" x="20" y="206" font-size="72" textLength="180" lengthAdjust="spacingAndGlyphs">You are</text>
  <text class="teal" x="20" y="288" font-size="92" textLength="180" lengthAdjust="spacingAndGlyphs">Unique</text>
  <text class="teal" transform="translate(250 400) rotate(-90)" font-size="38" textLength="200" lengthAdjust="spacingAndGlyphs">Revel in your</text>
  <text class="teal" transform="translate(281 408) rotate(-90)" font-size="40" textLength="242" lengthAdjust="spacingAndGlyphs">Individuality</text>

  <!-- Trust -->
  <text class="green" x="285" y="245" font-size="118" textLength="155" lengthAdjust="spacingAndGlyphs">Trust</text>
  <text class="green" x="288" y="285" font-size="31" textLength="180" lengthAdjust="spacingAndGlyphs">Your knowledge</text>
  <text class="green" x="288" y="313" font-size="31" textLength="178" lengthAdjust="spacingAndGlyphs">And seek advice</text>
  <text class="green" x="290" y="380" font-size="76" textLength="92" lengthAdjust="spacingAndGlyphs">Only</text>
  <text class="white" x="392" y="377" font-size="22" textLength="50" lengthAdjust="spacingAndGlyphs">From</text>
  <text class="white" x="290" y="405" font-size="25" textLength="172" lengthAdjust="spacingAndGlyphs">Respected sources</text>

  <!-- Do the right thing -->
  <text class="white" transform="translate(44 410) rotate(-90)" font-size="34" textLength="110" lengthAdjust="spacingAndGlyphs">Always</text>
  <text class="white" x="62" y="332" font-size="33" textLength="138" lengthAdjust="spacingAndGlyphs">Do the right</text>
  <text class="white" x="62" y="380" font-size="64" textLength="138" lengthAdjust="spacingAndGlyphs">Thing</text>
  <text class="white" x="62" y="400" font-size="18" textLength="138" lengthAdjust="spacingAndGlyphs">Without exception</text>

  <!-- Celebrate / diversity -->
  <text class="orange" x="20" y="478" font-size="88" textLength="220" lengthAdjust="spacingAndGlyphs">Celebrate</text>
  <text class="orange" x="20" y="500" font-size="22" textLength="190" lengthAdjust="spacingAndGlyphs">Of Australian culture</text>
  <text class="orange" x="258" y="435" font-size="22" textLength="204" lengthAdjust="spacingAndGlyphs">Respect and value the</text>
  <text class="orange" x="258" y="495" font-size="78" textLength="206" lengthAdjust="spacingAndGlyphs">Diversity</text>

  <!-- Support / champion -->
  <text class="green" x="20" y="541" font-size="50" textLength="175" lengthAdjust="spacingAndGlyphs">Support</text>
  <text class="green" x="20" y="566" font-size="28" textLength="175" lengthAdjust="spacingAndGlyphs">Your colleagues</text>
  <text class="green" transform="translate(210 505) rotate(90)" font-size="38" textLength="56" lengthAdjust="spacingAndGlyphs">And</text>
  <text class="green" x="257" y="530" font-size="42" textLength="207" lengthAdjust="spacingAndGlyphs">Champion</text>
  <text class="green" x="262" y="550" font-size="18" textLength="58" lengthAdjust="spacingAndGlyphs" letter-spacing="6">Their</text>
  <text class="green" x="258" y="572" font-size="26" textLength="95" lengthAdjust="spacingAndGlyphs">Purpose</text>
  <text class="white" x="362" y="560" font-size="36" textLength="103" lengthAdjust="spacingAndGlyphs">Choose</text>
  <text class="white" x="362" y="578" font-size="15" textLength="103" lengthAdjust="spacingAndGlyphs">Your thoughts wisely</text>

  <!-- Learn / reality -->
  <text class="orange" x="20" y="626" font-size="66" textLength="140" lengthAdjust="spacingAndGlyphs">Learn</text>
  <text class="orange" x="168" y="598" font-size="26" textLength="172" lengthAdjust="spacingAndGlyphs">Something</text>
  <text class="orange" x="168" y="616" font-size="24" textLength="172" lengthAdjust="spacingAndGlyphs">New each day</text>
  <text class="white" transform="translate(361 676) rotate(-90)" font-size="32" textLength="92" lengthAdjust="spacingAndGlyphs">Reality</text>
  <text class="white" x="372" y="640" font-size="70" textLength="93" lengthAdjust="spacingAndGlyphs">They</text>
  <text class="white" x="368" y="690" font-size="52" textLength="97" lengthAdjust="spacingAndGlyphs">Create</text>

  <!-- Lifelong learner -->
  <text class="white" x="20" y="680" font-size="34" textLength="28" lengthAdjust="spacingAndGlyphs">Be</text>
  <text class="white" x="20" y="712" font-size="34">A</text>
  <text class="white" x="20" y="748" font-size="30" textLength="90" lengthAdjust="spacingAndGlyphs">Lifelong</text>
  <text class="white" x="20" y="780" font-size="30" textLength="88" lengthAdjust="spacingAndGlyphs">Learner</text>

  <!-- Deliver / dream -->
  <text class="teal" x="118" y="705" font-size="86" textLength="218" lengthAdjust="spacingAndGlyphs">Deliver</text>
  <text class="teal" x="130" y="740" font-size="28" textLength="175" lengthAdjust="spacingAndGlyphs">Care skillfully</text>
  <text class="green" x="130" y="782" font-size="54" textLength="170" lengthAdjust="spacingAndGlyphs">Live your</text>
  <text class="green" transform="translate(310 700) rotate(90)" font-size="32" textLength="82" lengthAdjust="spacingAndGlyphs">Dream</text>

  <!-- Brand -->
  <g class="brand">
    <rect class="brand-panel" x="360" y="686" width="165" height="104" rx="6"/>
    <circle class="brand-dot" cx="386" cy="738" r="15"/>
    <text class="brand-name" x="410" y="736" font-size="24">CalmPeak</text>
    <text class="brand-name" x="410" y="762" font-size="24">For Nurses</text>
  </g>
</svg>
</body>
</html>
```